Responsive OnePage Design for recruitment company

BrightHire is a modern company that sources interim people for its customers. Mostly developers, scrum master, project managers and designers. In this website we want to tell something about us, about how we work, our customers and we want our candidates be able to subscribe. The subscription form should be several fields (name, surname, email address, phone number and the possibility to upload your resume.We want it to fit into a existing wordpress plugin. We also want a listing of our job opportunities. The listing should be designed in a clear readable overview and if you click on the job you should get the details and be able to respond quickly by filling in you name, surname, email address, rate, phone number and upload your resume. We want this to be a standard configurable plugin. It should be easy to fill in the jobs in Wordpress by our administrator. We want a fresh, modern and cool design. It should be a responsive onepage design. If you click on a listed job you should stay on the same page. Our logo is added.

Target Market(s)

recruitment

Industry/Entity Type

Recruitment

Font styles to use
Sans Serif

Colors

Designer to choose colors to be used in the design.

Requirements
Must have
• Onepage design
• listing of job opportunities
• subscription forms
• be responsive

```html
<!DOCTYPE html>
<html lang="en">
<head>
<meta charset="utf-8">
<title>BrightHire — Recruitment</title>
<link href="https://fonts.googleapis.com/css2?family=Roboto:wght@300;400;500;700&family=Roboto+Condensed:wght@400;700&family=Montserrat:wght@500&display=swap" rel="stylesheet">
<style>
:root{
  --blue:#1160b0;
  --blue-deep:#0b47a0;
  --ink:#1a1a1a;
  --text:#444;
  --muted:#666;
  --grey-icon:#7d7d7d;
  --row-border:#c9c9c9;
  --num:#d6e0eb;
  --white:#fff;
}
*{margin:0;padding:0;box-sizing:border-box}
html,body{width:1200px;height:3203px;overflow:hidden}
body{position:relative;background:var(--white);font-family:'Roboto',sans-serif;color:var(--ink)}
.abs{position:absolute}
.brand{font-family:'Montserrat',sans-serif;font-weight:500;letter-spacing:5px;font-size:31px;color:#333}
.brand b{font-weight:500;color:var(--blue)}
.site-header{left:0;top:0;width:1200px;height:75px;background:#fff}
.site-header .brand{left:100px;top:18px}
.nav{right:100px;top:25px;display:flex;gap:22px;font-size:16px;font-weight:500;color:#111}
.nav span.active{border-bottom:3px solid var(--blue);padding-bottom:4px}
.hero{left:0;top:75px;width:1200px;height:551px;background:linear-gradient(180deg,#7d8fa3 0%,#a9b8c7 45%,#6f8298 80%,#56677d 100%)}
.hero-title{left:137px;top:200px;font-size:56px;font-weight:700;line-height:56px;color:#111}
.hero-title em{font-style:normal;color:var(--blue)}
.hero-sub{left:143px;top:338px;font-size:31px;font-weight:300;color:#111}
.arrow{width:34px;height:34px}
.search{left:100px;top:542px;width:1004px;height:167px;background:var(--blue)}
.search h2{position:absolute;left:0;width:100%;top:20px;text-align:center;font-family:'Roboto Condensed',sans-serif;font-weight:700;font-size:41px;color:#fff}
.field{position:absolute;top:90px;height:37px;background:#fff;font-size:15px;color:#999;padding:9px 14px}
.upload{position:absolute;top:90px;left:799px;width:179px;height:37px;border:2px solid #fff;color:#fff;font-size:15px;padding:8px 10px;display:flex;justify-content:space-between;align-items:center}
.sec-title{left:0;width:1200px;text-align:center;font-family:'Roboto Condensed',sans-serif;font-weight:700;font-size:40px;color:#111}
.sec-title em{font-style:normal;color:var(--blue)}
.sec-sub{left:0;width:1200px;text-align:center;font-size:14px;color:#222}
.about-text{left:134px;top:914px;width:440px;font-family:'Roboto Condensed',sans-serif;font-size:16.5px;line-height:31px;color:#333}
.btn{background:var(--blue);color:#fff;font-weight:700;letter-spacing:3px;font-size:15px;display:flex;align-items:center;justify-content:center}
.about-frame{left:660px;top:946px;width:418px;height:254px;border:4px solid var(--blue)}
.about-photo{left:623px;top:914px;width:421px;height:256px;background:linear-gradient(135deg,#6b6d6e,#b39b6e 55%,#e9d9b0)}
.job{left:250px;width:700px;height:81px;border:2px solid var(--row-border);background:#fff}
.job .ico{position:absolute;left:0;top:0;width:90px;height:77px;background:var(--grey-icon);display:flex;align-items:center;justify-content:center}
.job .col{position:absolute;top:14px;width:140px;text-align:center;font-family:'Roboto Condensed',sans-serif;font-size:15px;color:#333;line-height:28px}
.job .col b{display:block;font-weight:700;color:#222}
.job .apply{position:absolute;left:566px;top:21px;width:117px;height:36px;font-size:14px;letter-spacing:.5px}
.step-num{font-family:'Roboto',sans-serif;font-weight:700;font-size:210px;color:var(--num);line-height:1}
.step-circle{width:170px;height:170px;border-radius:50%;background:var(--blue);border:5px solid #fff;box-shadow:0 0 0 4px var(--blue);display:flex;align-items:center;justify-content:center}
.step-title{width:300px;text-align:center;font-family:'Roboto Condensed',sans-serif;font-weight:700;font-size:20px;color:#222}
.step-text{width:210px;text-align:center;font-family:'Roboto Condensed',sans-serif;font-size:15.5px;line-height:26px;color:#555}
.client{font-family:'Roboto',sans-serif;font-weight:700;font-size:22px;color:#444;width:150px;text-align:center}
.footer{left:0;top:2887px;width:1200px;height:316px;background:var(--blue-deep)}
.newsletter{left:102px;top:2808px;width:1002px;height:106px;background:#fff;border:3px solid var(--blue-deep);box-shadow:0 3px 8px rgba(0,0,0,.25)}
.newsletter p{position:absolute;left:22px;top:24px;width:680px;font-size:16px;line-height:31px;color:#333}
.newsletter .btn{position:absolute;left:754px;top:24px;width:210px;height:48px;font-size:16px}
.footer .brand{color:#fff;left:100px;top:120px}
.footer .brand b{color:#fff}
.social{top:185px;display:flex;gap:22px;left:110px}
.social i{width:16px;height:16px;border-radius:50%;background:#fff;display:block}
.fcol{top:78px;color:#fff}
.fcol h4{font-size:16px;font-weight:700;margin-bottom:18px;letter-spacing:.5px}
.fcol p{font-size:12px;line-height:25px}
.rule{left:128px;top:241px;width:950px;height:1px;background:rgba(255,255,255,.35)}
.copy{left:0;top:271px;width:1200px;text-align:center;font-size:12px;color:#fff}
</style>
</head>
<body>

<header class="abs site-header">
  <div class="abs brand">BRIGHT<b>HIRE</b></div>
  <nav class="abs nav"><span class="active">HOME</span><span>ABOUT US</span><span>JOBS</span><span>HOW WE WORK</span><span>CUSTOMERS</span></nav>
</header>

<section class="abs hero" role="img" aria-label="City skyline photo with a man on a ladder looking through binoculars"></section>
<h1 class="abs hero-title">We offer <em>3,597</em> job<br>vacancies right now !</h1>
<p class="abs hero-sub">Find your desire one in a minute</p>
<svg class="abs arrow" style="left:54px;top:316px" viewBox="0 0 34 34"><circle cx="17" cy="17" r="15" fill="none" stroke="#fff" stroke-width="2"/><path d="M25 17H9M15 11l-6 6 6 6" fill="none" stroke="#fff" stroke-width="2"/></svg>
<svg class="abs arrow" style="left:1117px;top:316px" viewBox="0 0 34 34"><circle cx="17" cy="17" r="15" fill="none" stroke="#fff" stroke-width="2"/><path d="M9 17h16M19 11l6 6-6 6" fill="none" stroke="#fff" stroke-width="2"/></svg>

<form class="abs search">
  <h2>SEARCH FOR PROFESSIONALS</h2>
  <div class="field" style="left:34px;width:178px">Name</div>
  <div class="field" style="left:227px;width:177px">Surname</div>
  <div class="field" style="left:417px;width:177px">Email</div>
  <div class="field" style="left:609px;width:177px">Phone</div>
  <div class="upload">UPLOAD RESUME
    <svg width="20" height="20" viewBox="0 0 20 20"><path d="M10 13V3M6 7l4-4 4 4M3 11v6h14v-6" fill="none" stroke="#fff" stroke-width="2"/></svg>
  </div>
</form>

<h2 class="abs sec-title" style="top:788px">We Can Help You <em>Get A Job</em></h2>
<p class="abs sec-sub" style="top:848px">If the Job is online, you will find it on BrightHire</p>
<p class="abs about-text">Sed ut perspiciatis unde omnis iste natus error sit voluptatem accusantium doloremque laudantium, totam rem aperiam, eaque ipsa quae ab illo inventore veritatis et quasi architecto beatae vitae dicta sunt explicabo. Nemo enim ipsam voluptatem quia voluptas sit aspernatur aut odit aut fugit, sed quia consequuntur magni dolores eos qui ratione voluptatem</p>
<div class="abs btn" style="left:134px;top:1121px;width:182px;height:49px">READ MORE</div>
<div class="abs about-frame"></div>
<div class="abs about-photo" role="img" aria-label="Photo of clasped hands over a desk with charts and a laptop"></div>

<h2 class="abs sec-title" style="top:1318px">Browse Jobs <em>By Specialisms</em></h2>
<p class="abs sec-sub" style="top:1378px">33 jobs live - 0 added today.</p>

<div class="abs job" style="top:1458px"><div class="ico"><svg width="36" height="30" viewBox="0 0 36 30"><rect x="12" y="1" width="12" height="6" fill="none" stroke="#fff" stroke-width="3"/><rect x="0" y="7" width="36" height="23" rx="2" fill="#fff"/><rect x="0" y="15" width="36" height="2" fill="#7d7d7d"/><rect x="15" y="13" width="6" height="6" fill="#7d7d7d"/></svg></div><div class="col" style="left:103px"><b>POSITION</b>Developers</div><div class="col" style="left:235px"><b>LOCATION</b>New York</div><div class="col" style="left:376px"><b>EXPERIENCE</b>2+ Years</div><div class="btn apply">APPLY NOW</div></div>
<div class="abs job" style="top:1549px"><div class="ico"><svg width="36" height="30" viewBox="0 0 36 30"><rect x="12" y="1" width="12" height="6" fill="none" stroke="#fff" stroke-width="3"/><rect x="0" y="7" width="36" height="23" rx="2" fill="#fff"/><rect x="0" y="15" width="36" height="2" fill="#7d7d7d"/><rect x="15" y="13" width="6" height="6" fill="#7d7d7d"/></svg></div><div class="col" style="left:103px"><b>POSITION</b>Scrum Master</div><div class="col" style="left:235px"><b>LOCATION</b>Los Angeles</div><div class="col" style="left:376px"><b>EXPERIENCE</b>3+ Years</div><div class="btn apply">APPLY NOW</div></div>
<div class="abs job" style="top:1640px"><div class="ico"><svg width="36" height="30" viewBox="0 0 36 30"><rect x="12" y="1" width="12" height="6" fill="none" stroke="#fff" stroke-width="3"/><rect x="0" y="7" width="36" height="23" rx="2" fill="#fff"/><rect x="0" y="15" width="36" height="2" fill="#7d7d7d"/><rect x="15" y="13" width="6" height="6" fill="#7d7d7d"/></svg></div><div class="col" style="left:103px"><b>POSITION</b>Designer</div><div class="col" style="left:235px"><b>LOCATION</b>New York</div><div class="col" style="left:376px"><b>EXPERIENCE</b>1+ Years</div><div class="btn apply">APPLY NOW</div></div>
<div class="abs job" style="top:1731px"><div class="ico"><svg width="36" height="30" viewBox="0 0 36 30"><rect x="12" y="1" width="12" height="6" fill="none" stroke="#fff" stroke-width="3"/><rect x="0" y="7" width="36" height="23" rx="2" fill="#fff"/><rect x="0" y="15" width="36" height="2" fill="#7d7d7d"/><rect x="15" y="13" width="6" height="6" fill="#7d7d7d"/></svg></div><div class="col" style="left:103px"><b>POSITION</b>Project Manager</div><div class="col" style="left:235px"><b>LOCATION</b>Los Angeles</div><div class="col" style="left:376px"><b>EXPERIENCE</b>2+ Years</div><div class="btn apply">APPLY NOW</div></div>
<div class="abs job" style="top:1822px"><div class="ico"><svg width="36" height="30" viewBox="0 0 36 30"><rect x="12" y="1" width="12" height="6" fill="none" stroke="#fff" stroke-width="3"/><rect x="0" y="7" width="36" height="23" rx="2" fill="#fff"/><rect x="0" y="15" width="36" height="2" fill="#7d7d7d"/><rect x="15" y="13" width="6" height="6" fill="#7d7d7d"/></svg></div><div class="col" style="left:103px"><b>POSITION</b>Developers</div><div class="col" style="left:235px"><b>LOCATION</b>New York</div><div class="col" style="left:376px"><b>EXPERIENCE</b>3+ Years</div><div class="btn apply">APPLY NOW</div></div>

<h2 class="abs sec-title" style="top:2005px">How we <em>work</em></h2>
<p class="abs sec-sub" style="top:2063px">Lorem Ipsum is simply dummy text of</p>

<div class="abs step-num" style="left:95px;top:2120px">1</div>
<div class="abs step-num" style="left:468px;top:2120px">2</div>
<div class="abs step-num" style="left:858px;top:2120px">3</div>
<div class="abs step-circle" style="left:150px;top:2144px"><svg width="64" height="64" viewBox="0 0 64 64"><circle cx="28" cy="18" r="12" fill="#fff"/><path d="M6 56c0-14 10-22 22-22s22 8 22 22z" fill="#fff"/><circle cx="46" cy="46" r="11" fill="#fff" stroke="#1160b0" stroke-width="3"/><path d="M46 40v12M40 46h12" stroke="#1160b0" stroke-width="3"/></svg></div>
<div class="abs step-circle" style="left:538px;top:2144px"><svg width="60" height="60" viewBox="0 0 60 60"><path d="M30 38V8M19 19l11-11 11 11" fill="none" stroke="#fff" stroke-width="6"/><path d="M6 32v20h48V32" fill="none" stroke="#fff" stroke-width="6"/></svg></div>
<div class="abs step-circle" style="left:929px;top:2144px"><svg width="70" height="58" viewBox="0 0 70 58"><rect x="24" y="3" width="22" height="10" fill="none" stroke="#fff" stroke-width="5"/><rect x="2" y="13" width="66" height="43" rx="4" fill="#fff"/><rect x="2" y="28" width="66" height="3" fill="#1160b0"/><rect x="30" y="24" width="10" height="10" fill="#1160b0"/></svg></div>

<h3 class="abs step-title" style="left:85px;top:2334px">REGISTER YOUR NAME</h3>
<h3 class="abs step-title" style="left:473px;top:2334px">UPLOAD RESUME</h3>
<h3 class="abs step-title" style="left:864px;top:2334px">GET DESIRED JOB</h3>
<p class="abs step-text" style="left:130px;top:2366px">Lorem ipsum dolor sit amet, consectetur adipiscing elit, sed do eiusmod tempor incididunt</p>
<p class="abs step-text" style="left:518px;top:2366px">Lorem ipsum dolor sit amet, consectetur adipiscing elit, sed do eiusmod tempor incididunt</p>
<p class="abs step-text" style="left:909px;top:2366px">Lorem ipsum dolor sit amet, consectetur adipiscing elit, sed do eiusmod tempor incididunt</p>

<h2 class="abs sec-title" style="top:2539px">Our Esteemed <em>Customers</em></h2>
<p class="abs sec-sub" style="top:2599px">Lorem Ipsum is simply dummy text of</p>
<div class="abs client" style="left:117px;top:2683px">Norvale</div>
<div class="abs client" style="left:273px;top:2683px">Lumenpost</div>
<div class="abs client" style="left:435px;top:2683px">Techora</div>
<div class="abs client" style="left:593px;top:2683px">FieldCraft</div>
<div class="abs client" style="left:753px;top:2683px">Norvale</div>
<div class="abs client" style="left:913px;top:2683px">Kestrel Works</div>

<footer class="abs footer">
  <div class="abs brand">BRIGHT<b>HIRE</b></div>
  <div class="abs social"><i></i><i></i><i></i><i></i></div>
  <div class="abs fcol" style="left:536px"><h4>SUPPORT</h4><p>Help Center<br>Get Started<br>Contact US</p></div>
  <div class="abs fcol" style="left:681px"><h4>ABOUT US</h4><p>About Us<br>Terms of Use<br>Privacy Policy</p></div>
  <div class="abs fcol" style="left:854px"><h4>QUICK CONTACT</h4><p>Phone : 555.014.2290<br>Address : Harbor City, HC 20400<br>Mail : hello@brighthire.example</p></div>
  <div class="abs rule"></div>
  <p class="abs copy">© 2019 Reserved to BrightHire</p>
</footer>

<div class="abs newsletter">
  <p>Subscribe to BrightHire newsletter to get the latest jobs posted, candidates ,and other latest news stay updated !!</p>
  <div class="btn">SUBSCRIBE</div>
</div>

</body>
</html>
```